Window Treatment business needs website redesigned.

We need a revamp and refresh of our current site www.velmarix.ca
Looking to attract very high end customer. It should be a very simple design with very little text. This site will be visited by prospective homeowners, designers, builders and architects. They should feel that they are dealing with a high-end product selection, where experience, customer service and unique product offering is the focus. The content will be to highlight our services and highlight the manufacturers we sell, using a few rich photos to highlight the products. We should NOT look like we are a very large company. It should NOT have discounts/savings buttons and many menus to choose from. We offer over 15 years experience to narrow the many market options, to provide the right technical solution.
We specialize in products that are not readily available on the market and specifically motorized systems for indoors and outdoors.
Our main suppliers are Kravenholt.com, Dimbrell.com
We carry our own locally manufactured product line of roller shades.
Main product pictures should be of roller shades, outdoor bug screens, awnings and outdoor pergolas.

Reason: I understand that Christmas is coming up real short and many people are extremely busy. If you have a CREATIVE gifting you still want to submit, I look forward to your idea!

Reason: Due to holiday season, we have not had sufficient time to review to make a final decision. Thank you for your patience!

Target Market(s)

High end home owners, designers, builders, architects

Industry/Entity Type

Contractor

Coding

Coded - Design and coding required

Number of Pages Required

3 page

Font styles to use
Sans Serif

Requirements
Must have
• Landing page with full size image like homepage of zolvane.it
• Products page that highlights products with simple product shot image, description and link to manufacturer.
• On main page a scrolling of customer reviews.
• I want a very simple, eye-catching, emotional image for homepage. It does not need to include any product image.
• An image that shows technology combining/meshing with hand craftsmanship.
• Focus is on design.
• http://www.zolvane.it/en/gallery is a great layout and design.
Nice to have
• Logo shape for icons and watermark should be used.
• Look like and have simple motion effects like quorix.com or telvarin.com
Should not have
• Generic/standard looking feel like bluppet.com or mecklorwindow.ca
• No use of green as background only subtle text.
• Lots of text and pages.

```html
<!DOCTYPE html>
<html lang="en">
<head>
<meta charset="utf-8">
<title>Velmarix – Window Treatment Solutions</title>
<link rel="stylesheet" href="https://fonts.googleapis.com/css2?family=Montserrat:wght@300;400;500;600;700&family=Open+Sans:wght@400;600&display=swap">
<style>
:root{
  --green:#8cc63f;
  --green-dark:#6fa82c;
  --ink:#1d1d1d;
  --text:#444;
  --white:#fff;
  --head:'Montserrat',sans-serif;
  --body:'Open Sans',sans-serif;
}
*{box-sizing:border-box;margin:0;padding:0}
html,body{width:1200px;height:4317px;overflow:hidden}
body{position:relative;background:var(--white);font-family:var(--body);color:var(--text)}
h1,h2,h3,h4{font-weight:400}
.abs{position:absolute}
svg{display:block}

/* hero */
.hero{left:0;top:0;width:1200px;height:705px;
  background:linear-gradient(100deg,rgba(255,255,255,.0) 0%,rgba(255,255,255,.35) 45%,rgba(60,70,55,.0) 100%),
  linear-gradient(180deg,#e9ecea 0%,#cdd5cc 22%,#9fb08f 42%,#d8d4cc 58%,#a68a68 78%,#5e4a38 100%)}
.brand{left:78px;top:34px;display:flex;align-items:center;gap:14px}
.brand-dot{width:76px;height:76px;border-radius:50%;background:var(--ink)}
.brand-name{font-family:var(--head);font-weight:500;font-size:42px;color:var(--ink);line-height:1}
.brand-tag{font-family:var(--body);font-size:14px;color:var(--green-dark);margin-top:4px}
.nav{left:490px;top:52px;width:710px;height:68px;background:rgba(255,255,255,.92);border-radius:34px 0 0 34px;display:flex;align-items:center;justify-content:space-around;padding:0 30px}
.nav a{font-family:var(--head);font-size:16px;color:#333;text-decoration:none;letter-spacing:.5px}
.nav a.is-active{color:var(--green)}
.hero-title{left:268px;top:312px;width:696px;height:88px;background:rgba(40,40,40,.62);color:var(--white);font-family:var(--head);font-weight:300;font-size:54px;text-align:center;line-height:88px;letter-spacing:.5px}
.hero-sub{left:240px;top:418px;width:720px;height:38px;background:var(--green);color:var(--white);font-family:var(--head);font-size:17px;text-align:center;line-height:38px;letter-spacing:.3px}
.hero-curve{left:0;top:480px}

/* welcome */
.welcome-title{left:80px;top:770px;font-family:var(--head);font-weight:400;font-size:60px;line-height:1.15;color:var(--ink);letter-spacing:1px}
.welcome-title span{color:var(--green);display:block}
.welcome-text{left:80px;top:930px;width:470px;font-size:15px;line-height:1.6}
.btn-more{left:80px;top:1055px;width:174px;height:52px;border:2px solid var(--ink);border-radius:26px;font-family:var(--head);font-weight:500;font-size:16px;color:var(--ink);display:flex;align-items:center;justify-content:center;gap:8px}
.welcome-visual{left:560px;top:755px;width:520px;height:350px;background:radial-gradient(ellipse at 45% 45%,#c9ccd0 0%,#e3e5e8 40%,#f5f5f5 70%,#fff 100%)}

/* services */
.band{left:0;width:1200px}
.band-roller{background:linear-gradient(90deg,#1c1f22 0%,#33373a 40%,#2a2d2f 70%,#16181a 100%)}
.band-drape{background:linear-gradient(90deg,#dcdad4 0%,#f4f3ef 35%,#ebe9e3 65%,#d2d0c9 100%)}
.band-awning{background:linear-gradient(180deg,#1b2028 0%,#2f3540 45%,#4a3b34 75%,#1d1a1a 100%)}
.band-bug{background:linear-gradient(90deg,#c9c2b3 0%,#eeebe4 30%,#f6f5f1 55%,#d3cbbb 100%)}
.services-top{left:0;top:1110px}
.services-title{left:0;top:1205px;width:1200px;text-align:center;font-family:var(--head);font-size:42px;color:var(--green);letter-spacing:1px}
.svc-title{font-family:var(--head);font-weight:400;font-size:36px;letter-spacing:.5px}
.svc-title b{font-weight:600}
.svc-title.on-dark{color:var(--green)}
.svc-title.on-light{color:var(--ink)}
.svc-text{width:560px;font-size:15px;line-height:1.55}
.on-dark-text{color:#ddd}
.on-light-text{color:#444}
.svc-icon{width:210px;height:210px}

/* testimonial */
.testi{left:0;top:2620px;width:1200px;height:410px}
.testi-title{left:0;top:2680px;width:1200px;text-align:center;font-family:var(--head);font-size:40px;color:var(--white);letter-spacing:1px}
.testi-title span{color:var(--green)}
.quote-mark{left:570px;top:2750px;font-family:var(--head);font-weight:700;font-size:90px;color:var(--green);line-height:1}
.testi-text{left:110px;top:2830px;width:980px;text-align:center;color:#ddd;font-size:15.5px;line-height:1.7}
.testi-name{left:0;top:2902px;width:1200px;text-align:center;font-family:var(--head);font-size:15px;color:var(--green);letter-spacing:1px}
.dots{left:560px;top:2940px;display:flex;gap:10px}
.dots i{width:14px;height:14px;border-radius:50%;background:#777;display:block}
.dots i.on{background:var(--white)}

/* gallery */
.gal-title{left:0;top:3065px;width:1200px;text-align:center;font-family:var(--head);font-size:42px;color:var(--ink);letter-spacing:1px}
.gal-title span{color:var(--green);font-weight:500}
.gal-text{left:250px;top:3135px;width:700px;text-align:center;font-size:15px;line-height:1.6}
.filters{left:205px;top:3216px;display:flex;gap:18px}
.filters span{height:52px;padding:0 34px;border:1px solid #ccc;border-radius:26px;font-family:var(--head);font-size:15px;color:#555;display:flex;align-items:center}
.filters span.on{background:#111;color:var(--white);border-color:#111}
.grid{left:0;top:3301px;width:1200px;height:417px;display:grid;grid-template-columns:repeat(4,300px);grid-template-rows:repeat(2,208.5px)}
.ph{width:100%;height:100%}
.ph-1{background:linear-gradient(180deg,#3b3a35 0%,#b9c3bd 30%,#7f9268 60%,#5c4a38 100%)}
.ph-2{background:linear-gradient(180deg,#eef1f2 0%,#c7d0c6 40%,#6f8a58 75%,#4c4a3f 100%)}
.ph-3{background:var(--green);display:flex;align-items:center;justify-content:center}
.ph-4{background:linear-gradient(160deg,#2f5c7c 0%,#6d7f86 35%,#9c7a56 65%,#3d2f25 100%)}
.ph-5{background:linear-gradient(180deg,#dfe4e6 0%,#bfc8cb 45%,#5f7a45 80%,#3f4c2f 100%)}
.ph-6{background:linear-gradient(180deg,#a8c3d8 0%,#eef0ee 35%,#737b6f 65%,#4b5a3c 100%)}
.ph-7{background:linear-gradient(180deg,#7fb2da 0%,#c5dbe8 35%,#6d8f4a 65%,#3c5a2c 100%)}
.ph-8{background:linear-gradient(180deg,#2b2824 0%,#7c8b70 40%,#a48e73 70%,#3a2f26 100%)}

/* partners */
.partners{left:0;top:3718px;width:1200px;height:167px;display:flex;align-items:center;justify-content:space-around;padding:0 60px}
.partner{display:flex;align-items:center;gap:8px;font-family:var(--head);font-weight:600;font-size:24px;color:#3a3a3a}
.partner i{width:22px;height:22px;background:#3a3a3a;display:block}

/* footer */
.footer-curve{left:0;top:3885px}
.footer{left:0;top:3985px;width:1200px;height:275px;background:linear-gradient(180deg,#26292c,#1a1c1e)}
.f-head{font-family:var(--head);font-weight:500;font-size:19px;color:var(--white);letter-spacing:1px}
.f-links{left:80px;top:4050px;list-style:none;font-size:14px;line-height:33px;color:#ccc}
.f-contact{left:345px;top:4055px;font-size:14px;color:#ccc;line-height:1.6}
.f-row{display:flex;gap:14px;align-items:flex-start;margin-bottom:12px}
.f-row b{color:var(--green);font-weight:600}
.map{left:620px;top:3995px;width:200px;height:200px;border-radius:50%;background:radial-gradient(circle,#eef0ea,#cdd3c8);border:6px solid #eee}
.f-brand{left:905px;top:4045px;display:flex;align-items:center;gap:10px}
.f-brand i{width:44px;height:44px;border-radius:50%;background:var(--white);display:block}
.f-brand span{font-family:var(--head);font-weight:600;font-size:28px;color:var(--white)}
.social{left:922px;top:4122px;display:flex;gap:14px}
.social i{width:44px;height:44px;border-radius:50%;background:var(--white);display:block}
.copy{left:0;top:4260px;width:1200px;height:57px;background:#0c0c0c;color:#ddd;text-align:center;line-height:57px;font-size:14px}
.copy b{color:var(--white)}
</style>
</head>
<body>

<!-- hero -->
<div class="abs hero" role="img" aria-label="Bright modern living room with large windows, garden view and roller shades"></div>
<div class="abs brand">
  <span class="brand-dot"></span>
  <div><div class="brand-name">Velmarix</div><div class="brand-tag">Window Treatment Solutions</div></div>
</div>
<nav class="abs nav">
  <a class="is-active" href="#">HOME</a><a href="#">ABOUT</a><a href="#">SERVICES</a><a href="#">PRODUCTS</a><a href="#">GALLERY</a><a href="#">CONTACT</a>
</nav>
<h1 class="abs hero-title">Roman Skylight System</h1>
<p class="abs hero-sub">INSTANT HEAT REDUCTION USING ROLLERS, OR STATIONARY SCREENS.</p>
<svg class="abs hero-curve" width="1200" height="230" viewBox="0 0 1200 230">
  <path d="M0,40 Q500,270 1200,80 L1200,230 L0,230Z" fill="#111"/>
  <path d="M0,110 Q520,300 1200,110 L1200,230 L0,230Z" fill="#fff"/>
</svg>

<!-- welcome -->
<h2 class="abs welcome-title">WELCOME TO<span>VELMARIX</span></h2>
<p class="abs welcome-text">Lorem Ipsum is simply dummy text of the printing and typesetting industry. Lorem Ipsum has been the industry's standard dummy text ever since the 1500s, when an unknown printer took a galley of type and scrambled it to...</p>
<div class="abs btn-more">READ MORE <svg width="16" height="14" viewBox="0 0 16 14"><path d="M2 2l5 5-5 5M8 2l5 5-5 5" fill="none" stroke="#1d1d1d" stroke-width="2"/></svg></div>
<div class="abs welcome-visual" role="img" aria-label="Architectural cutaway model of a home interior with blueprints"></div>

<!-- services -->
<div class="abs band band-roller" style="top:1137px;height:489px" role="img" aria-label="Dark interior with motorized roller shades"></div>
<svg class="abs services-top" width="1200" height="90" viewBox="0 0 1200 90">
  <path d="M0,0 L1200,0 L1200,30 Q600,110 0,30Z" fill="#fff"/>
</svg>
<h2 class="abs services-title">SERVICES</h2>

<h3 class="abs svc-title on-dark" style="left:80px;top:1390px">ROLLER SHADES</h3>
<p class="abs svc-text on-dark-text" style="left:80px;top:1448px">Lorem Ipsum is simply dummy text of the printing and typesetting industry Lorem Ipsum has been the industry's standard dummy text ever since the 1500s.</p>
<svg class="abs svc-icon" style="left:787px;top:1348px" viewBox="0 0 210 210">
  <circle cx="105" cy="105" r="100" fill="#fff" stroke="#111" stroke-width="8"/>
  <rect x="60" y="60" width="90" height="92" rx="4" fill="none" stroke="#111" stroke-width="7"/>
  <rect x="60" y="60" width="90" height="46" fill="#111"/>
  <path d="M72 74h66M72 88h66" stroke="#fff" stroke-width="4"/>
</svg>

<div class="abs band band-drape" style="top:1626px;height:337px" role="img" aria-label="Light room with sheer drapery"></div>
<svg class="abs svc-icon" style="left:206px;top:1685px" viewBox="0 0 210 210">
  <circle cx="105" cy="105" r="100" fill="#fff" stroke="#111" stroke-width="8"/>
  <rect x="52" y="55" width="106" height="12" fill="#111"/>
  <path d="M62 67v88h18c-4-30-4-60 0-88zM148 67v88h-18c4-30 4-60 0-88z" fill="#111"/>
</svg>
<h3 class="abs svc-title on-light" style="left:555px;top:1725px">DRAPERY</h3>
<p class="abs svc-text on-light-text" style="left:555px;top:1780px">Lorem Ipsum is simply dummy text of the printing and typesetting industry. Lorem Ipsum has been the industry's standard dummy text ever since the 1500s.</p>

<div class="abs band band-awning" style="top:1963px;height:331px" role="img" aria-label="Terrace with retractable awning at dusk"></div>
<h3 class="abs svc-title on-dark" style="left:80px;top:2058px">AWNINGS</h3>
<p class="abs svc-text on-dark-text" style="left:80px;top:2115px">Lorem Ipsum is simply dummy text of the printing and typesetting industry. Lorem Ipsum has been the industry's standard dummy text ever since the 1500s.</p>
<svg class="abs svc-icon" style="left:787px;top:2010px" viewBox="0 0 210 210">
  <circle cx="105" cy="105" r="100" fill="#fff" stroke="#111" stroke-width="8"/>
  <path d="M55 80l12-22h76l12 22z" fill="#111"/>
  <path d="M55 80q12 14 25 0q12 14 25 0q12 14 25 0q12 14 25 0" fill="none" stroke="#111" stroke-width="6"/>
  <rect x="65" y="95" width="80" height="60" fill="none" stroke="#111" stroke-width="7"/>
  <rect x="93" y="118" width="24" height="37" fill="#111"/>
</svg>

<div class="abs band band-bug" style="top:2294px;height:382px" role="img" aria-label="Bright room with woven roman shades"></div>
<svg class="abs svc-icon" style="left:206px;top:2330px" viewBox="0 0 210 210">
  <circle cx="105" cy="105" r="100" fill="#fff" stroke="#111" stroke-width="8"/>
  <rect x="58" y="55" width="94" height="14" fill="#111"/>
  <rect x="66" y="69" width="78" height="84" fill="none" stroke="#111" stroke-width="7"/>
  <path d="M66 100h78M105 69v84" stroke="#111" stroke-width="4"/>
</svg>
<h3 class="abs svc-title on-light" style="left:555px;top:2390px">BUG <b>SCREENS</b></h3>
<p class="abs svc-text on-light-text" style="left:555px;top:2448px">Lorem Ipsum is simply dummy text of the printing and typesetting industry. Lorem Ipsum has been the industry's standard dummy text ever since the 1500s.</p>

<!-- testimonial -->
<svg class="abs testi" viewBox="0 0 1200 410">
  <path d="M0,80 Q600,0 1200,70 L1200,410 L0,410Z" fill="#111"/>
</svg>
<h2 class="abs testi-title">WHAT OUR <span>CLIENT SAY</span></h2>
<div class="abs quote-mark">&ldquo;</div>
<p class="abs testi-text">"Lorem Ipsum is simply dummy text of the printing and typesetting industry. Lorem Ipsum has been the industry's standard dummy text ever since the 1500s, when an unknown printer took a galley of type and scrambled it to make a"</p>
<p class="abs testi-name">— CLIENT NAME</p>
<div class="abs dots"><i class="on"></i><i class="on"></i><i class="on"></i><i></i></div>

<!-- gallery -->
<h2 class="abs gal-title">OUR <span>GALLARY</span></h2>
<p class="abs gal-text">Lorem Ipsum is simply dummy text of the printing and typesetting industry. Lorem Ipsum has been the industry's standard dummy text ever since the 1500s, when an unknown printer took a</p>
<div class="abs filters"><span class="on">All</span><span>Roller Shades</span><span>Drapery</span><span>Outdoor Bug Screens</span><span>Awnings</span></div>
<div class="abs grid">
  <div class="ph ph-1" role="img" aria-label="Covered patio with outdoor screens"></div>
  <div class="ph ph-2" role="img" aria-label="Modern pergola terrace"></div>
  <div class="ph ph-3" role="img" aria-label="Highlighted gallery item">
    <svg width="56" height="56" viewBox="0 0 56 56"><circle cx="24" cy="24" r="16" fill="none" stroke="#fff" stroke-width="4"/><path d="M36 36l14 14M24 16v16M16 24h16" stroke="#fff" stroke-width="4"/></svg>
  </div>
  <div class="ph ph-4" role="img" aria-label="Living room with lake view and motorized shades"></div>
  <div class="ph ph-5" role="img" aria-label="Exterior vertical screens on a facade"></div>
  <div class="ph ph-6" role="img" aria-label="Glass pavilion with retractable screens"></div>
  <div class="ph ph-7" role="img" aria-label="Panoramic window view over landscape"></div>
  <div class="ph ph-8" role="img" aria-label="Dining room with sheer roller shades"></div>
</div>

<!-- partners -->
<div class="abs partners">
  <span class="partner">Dimbrell</span>
  <span class="partner"><i></i>Harnquist</span>
  <span class="partner">Quietrail</span>
  <span class="partner">Solvenn</span>
  <span class="partner"><i></i>Tarvelle</span>
  <span class="partner">Brightlen</span>
</div>

<!-- footer -->
<svg class="abs footer-curve" width="1200" height="102" viewBox="0 0 1200 102">
  <path d="M0,102 L0,70 Q600,-40 1200,40 L1200,102Z" fill="#8cc63f"/>
  <path d="M0,102 L0,95 Q600,-10 1200,70 L1200,102Z" fill="#26292c"/>
</svg>
<div class="abs footer"></div>
<h4 class="abs f-head" style="left:80px;top:4010px">USEFUL LINKS</h4>
<ul class="abs f-links"><li>Home</li><li>Blog</li><li>Privacy Policy</li><li>Terms of Use</li><li>Contact Us</li></ul>
<h4 class="abs f-head" style="left:345px;top:4010px">CONTACT US</h4>
<div class="abs f-contact">
  <div class="f-row"><svg width="16" height="22" viewBox="0 0 16 22"><path d="M8 0a8 8 0 0 0-8 8c0 6 8 14 8 14s8-8 8-14a8 8 0 0 0-8-8z" fill="#fff"/><circle cx="8" cy="8" r="3" fill="#26292c"/></svg><div><b>VELMARIX</b><br>12 Orlen Way,<br>Toronto, ON, M4G 0A0</div></div>
  <div class="f-row"><svg width="16" height="16" viewBox="0 0 16 16"><path d="M3 1l3 3-2 2c1 2 3 4 5 5l2-2 3 3-2 3C7 15 1 9 1 3z" fill="#fff"/></svg>555-014-2290</div>
  <div class="f-row"><svg width="18" height="14" viewBox="0 0 18 14"><rect width="18" height="14" rx="2" fill="#fff"/><path d="M1 2l8 6 8-6" fill="none" stroke="#26292c" stroke-width="1.5"/></svg>info@velmarix.ca</div>
</div>
<div class="abs map" role="img" aria-label="Location map of the showroom"></div>
<div class="abs f-brand"><i></i><span>Velmarix</span></div>
<div class="abs social"><i></i><i></i><i></i></div>
<div class="abs copy">© <b>VELMARIX</b> - 2016. All Rights Reserved</div>

</body>
</html>
```